Business Cards for company that supports physicians that do medical research

Need to create a business card for Qorvel Studies (www.qorvelstudies.example), a company devoted to supporting physicians who conduct medical research. The form of the card should match the message of research and information quest. I have provided the logo of the company as an uploaded file. Designs should be simple and slick aimed at very high end clients.

Target Market(s)

Medical doctors that are also researchers

Industry/Entity Type

Medical

Contact Information for Business Card

Should feature logo and fields for personal info:
Name/title
Phone /email

Font styles to use
Serif
Sans Serif

Requirements
Must have
• Qorvel logo and fields for personal info:
• Name: Bertrand Okonfu
• Title: VP Research and Senior Analyst
• Phone: 555-203-4719
• email: info@qorvelstudies.example
Nice to have
• Interesting cards that I've seen:
• 1- all black/charcoal or very dark background
• 2- Plastic - semi-transparent
• 3- non-standard height-width ratios
• 4- Functional cards -- USB drive incorporated
Should not have
• Too busy; needs to stay very simple

```html
<!DOCTYPE html>
<html lang="en">
<head>
<meta charset="utf-8">
<title>Qorvel Studies — Business Card</title>
<link rel="stylesheet" href="https://fonts.googleapis.com/css2?family=Open+Sans:ital,wght@0,400;0,600;0,700;1,400&display=swap">
<style>
  :root {
    --backdrop: #3b3b3b;
    --brand-blue: #1b7ec2;
    --brand-blue-light: #4a9ad2;
    --card-white: #f7f7f7;
    --ink: #4a4a4a;
    --white: #ffffff;
  }
  * { box-sizing: border-box; margin: 0; padding: 0; }
  html, body {
    width: 1200px; height: 750px; overflow: hidden;
    background: var(--backdrop);
    font-family: "Open Sans", Arial, sans-serif;
  }
  .stage { position: relative; width: 1200px; height: 750px; }
  .card {
    position: absolute; top: 228px;
    width: 461px; height: 262px; overflow: hidden;
  }
  .card--front { left: 124px; background: var(--card-white); }
  .card--back { left: 618px; background: var(--brand-blue); }

  .card__header-art {
    position: absolute; left: 0; top: 0;
    width: 461px; height: 82px;
    background: linear-gradient(180deg, var(--brand-blue) 0%, var(--brand-blue) 60%, var(--brand-blue-light) 100%);
  }

  .holder {
    position: absolute; right: 25px; top: 14px;
    text-align: right; color: var(--white);
  }
  .holder__name { font-size: 17px; font-weight: 600; line-height: 22px; }
  .holder__title { font-size: 12px; font-weight: 400; line-height: 16px; }

  .wordmark {
    position: absolute; left: 38px; top: 104px;
    font-size: 25px; font-weight: 600; color: var(--brand-blue);
    line-height: 1;
  }

  .contacts {
    position: absolute; left: 38px; top: 184px;
    list-style: none; font-size: 11px; color: var(--ink);
  }
  .contacts li { display: flex; align-items: center; height: 17.5px; }
  .contacts svg { width: 11px; height: 11px; margin-right: 7px; fill: var(--brand-blue); }

  .card--back .wordmark {
    left: auto; right: 27px; top: 176px;
    color: var(--white); font-size: 24px;
  }
  .back__url {
    position: absolute; right: 27px; top: 230px;
    font-size: 11px; font-style: italic; color: var(--white);
    letter-spacing: 1.4px;
  }
</style>
</head>
<body>
<main class="stage">
  <section class="card card--front" aria-label="Card front">
    <div class="card__header-art" role="img" aria-label="Header area with flowing blue, grey and green swoosh decoration"></div>
    <div class="holder">
      <p class="holder__name">Bertrand Okonfu</p>
      <p class="holder__title">VP Research &amp; Senior Analyst</p>
    </div>
    <p class="wordmark">Qorvel Studies</p>
    <ul class="contacts">
      <li><svg viewBox="0 0 24 24"><path d="M6.6 10.8a15.1 15.1 0 0 0 6.6 6.6l2.2-2.2a1 1 0 0 1 1-.25 11.4 11.4 0 0 0 3.6.57 1 1 0 0 1 1 1V20a1 1 0 0 1-1 1A17 17 0 0 1 3 4a1 1 0 0 1 1-1h3.5a1 1 0 0 1 1 1c0 1.25.2 2.45.57 3.57a1 1 0 0 1-.25 1z"/></svg>555-203-4719</li>
      <li><svg viewBox="0 0 24 24"><path d="M2 5h20v14H2z M4 7v1l8 5 8-5V7l-8 5z" fill-rule="evenodd"/></svg>info@qorvelstudies.example</li>
      <li><svg viewBox="0 0 24 24"><circle cx="12" cy="12" r="10"/></svg>www.qorvelstudies.example</li>
    </ul>
  </section>

  <section class="card card--back" aria-label="Card back">
    <p class="wordmark">Qorvel Studies</p>
    <p class="back__url">www.qorvelstudies.example</p>
  </section>
</main>
</body>
</html>
```